complete redesign of VitalPlate.com

VITALPLATE.COM
MAIN MANU

We need it cut into HTML / Wordpress Friendly.... Our developer will handle all the WP / PHP coding, but we need it placed into HTML format so he can put into wordpress.

Please see the old vitalplate.com by visiting www.vitalplate.com... we want something completely different, but... just use this site for reference as to audience, theme, etc... we want something where it is science meets diet in helping fight cancer :)

WE NEED SOMETHING MORE MODERN AND MEDICAL IN TERMS OF DESIGN

See below:

1 CANCER NEWS
2 NUTRITION DIAGNOSTICS
3 DIET STEPS
4 DIET SUPPLEMENTS IN CANCER 
5 DICTIONARY OF MARKINGS ON FOOD
6 MERIBLEND VIDEOS
7 YOUR INDIVIDUAL DIET - SUBSCRIPTION

a. CANCER NEWS - latest articles relating to cancer prevention research treatments

b. NUTRITION DIAGNOSTICS -  description of the research that must be done to determine the degree of malnutrition of the body a place on the charts
pictures, etc.

c. DIET STEPS 
(sub menu - @)
¥ prevention of oncological - @
¥ diet chemotherapy - @
¥ diet in radiotherapy - @
¥ hormonal diet - @
¥ diet during convalescence - @

d. DIET SUPPLEMENTS IN CANCER - articles describing various supplements summary tables, etc.

e. DICTIONARY OF MARKINGS ON FOOD - composition, translation of labels on food, itd.

f. MERIBLEND VIDEOS 
(sub menu - @)
¥ healthy cooking - @
¥ meal preparation - @
¥ storage of food - @
¥ eco food - @
¥ rehabilitation - @
¥ yoga - @
¥ exercises - @
¥ psycho-oncology training - @
¥ music therapy - @

g. YOUR INDIVIDUAL DIET -  individual personalized diet for subscribing. We
add this point by developing a system of diet.

After 3 months, we will add special individual programs that mix diet, exercise and psychological lectures

Industry/Entity Type

Medical

Logo Text

Vital Plate / VitalPlate.com

Number of Pages Required

5+ page

Font styles to use
Sans Serif

Colors
ec1f27
9bcb3c
ffffff

Requirements
Must have
• HTML/CSS

```html
<!DOCTYPE html>
<html lang="en">
<head>
<meta charset="utf-8">
<title>Vital Plate</title>
<link href="https://fonts.googleapis.com/css2?family=Abel&family=Roboto:wght@400;500&display=swap" rel="stylesheet">
<style>
:root{
  --green:#179a40;
  --green-text:#1f9a45;
  --dark:#333333;
  --darker:#1e1e1e;
  --nav-active:#4a4a4a;
  --ink:#444444;
  --muted:#777777;
  --panel:#f0f0f0;
  --white:#ffffff;
  --line:#cfcfcf;
}
*{box-sizing:border-box;margin:0;padding:0}
html,body{width:835px;height:1200px;overflow:hidden}
body{position:relative;background:var(--white);font-family:'Roboto',Arial,sans-serif;color:var(--ink)}
.site-header{position:absolute;left:0;top:0;width:835px;height:77px}
.brand{position:absolute;left:92px;top:14px;display:flex;align-items:center;gap:10px}
.brand-dot{width:30px;height:30px;border-radius:50%;background:var(--green)}
.brand-name{font-family:'Abel',sans-serif;font-size:33px;color:#3a3a3a;line-height:1}
.search{position:absolute;left:622px;top:21px;width:120px;height:25px;border:1px solid var(--line);font-size:7px;color:#888;padding:8px 10px}
.search svg{position:absolute;right:8px;top:7px}
.main-nav{position:absolute;left:0;top:77px;width:835px;height:27px;background:var(--dark)}
.main-nav ul{list-style:none;display:flex;position:absolute;left:92px;top:0;height:27px}
.main-nav li{font-size:7.2px;color:#e6e6e6;padding:0 7.8px;line-height:27px;letter-spacing:.1px}
.main-nav li.active{background:var(--nav-active)}
.hero{position:absolute;left:0;top:104px;width:835px;height:278px;
  background:radial-gradient(circle at 15% 40%,#7fa33a 0,transparent 22%),
  radial-gradient(circle at 85% 45%,#e8e2da 0,transparent 30%),
  linear-gradient(100deg,#b8202a 0%,#7a1a2c 35%,#c42430 60%,#d9c9c0 85%,#f2eeea 100%)}
.hero-caption{position:absolute;left:337px;top:202px;width:161px;height:30px;background:rgba(20,20,20,.8);color:var(--white);font-family:'Abel',sans-serif;font-size:17px;text-align:center;line-height:30px}
.hero-dots{position:absolute;left:396px;top:247px;display:flex;gap:6px}
.hero-dots span{width:6px;height:6px;border-radius:50%;border:1px solid var(--white)}
.hero-dots span.on{background:var(--white)}
.welcome{position:absolute;left:92px;top:416px;width:651px;text-align:center}
.welcome h1{font-family:'Abel',sans-serif;font-weight:400;font-size:23px;color:var(--green-text)}
.welcome p{margin-top:8px;font-size:7.4px;line-height:13.5px;color:#666}
.section-title{font-family:'Abel',sans-serif;font-weight:400;font-size:22px;color:var(--green-text);position:absolute;left:92px}
.arrows{position:absolute;left:722px;display:flex;gap:7px}
.news{position:absolute;left:0;top:544px;width:835px;height:255px;background:var(--panel)}
.cards{position:absolute;left:93px;display:flex;gap:26px}
.card{width:199px}
.card-media{position:relative;width:199px;height:111px}
.card p{margin-top:9px;font-size:7.4px;line-height:11.3px;color:#444}
.card .more{display:block;margin-top:6px;font-size:6.6px;color:var(--muted);letter-spacing:.3px}
.play{position:absolute;left:91px;top:47px}
.newsletter{position:absolute;left:0;top:799px;width:835px;height:55px;background:var(--green)}
.newsletter h2{position:absolute;left:135px;top:14px;font-family:'Abel',sans-serif;font-weight:400;font-size:21px;color:var(--white)}
.field{position:absolute;top:15px;width:149px;height:27px;background:var(--white);font-size:7.4px;color:#555;padding:9px 10px}
.btn{position:absolute;left:639px;top:15px;width:59px;height:27px;background:#222;color:var(--white);font-family:'Abel',sans-serif;font-size:10px;text-align:center;line-height:27px;border-radius:2px}
.site-footer{position:absolute;left:0;top:1110px;width:835px;height:90px;background:var(--darker)}
.footer-nav{position:absolute;left:0;top:18px;width:835px;text-align:center;font-size:6.8px;color:#bbb;letter-spacing:.1px}
.footer-nav span{margin:0 4px}
.footer-rule{position:absolute;left:92px;top:45px;width:651px;height:1px;background:#3a3a3a}
.copyright{position:absolute;left:92px;top:63px;font-size:6.8px;color:#bbb}
.social{position:absolute;left:566px;top:58px;display:flex;gap:5.5px}
.social span{width:18px;height:18px;border-radius:50%;background:#5a5a5a}
</style>
</head>
<body>
<header class="site-header">
  <div class="brand"><span class="brand-dot"></span><span class="brand-name">Vital Plate</span></div>
  <div class="search">Search
    <svg width="9" height="9" viewBox="0 0 10 10"><circle cx="4" cy="4" r="3" fill="none" stroke="#777" stroke-width="1.3"/><line x1="6.3" y1="6.3" x2="9" y2="9" stroke="#777" stroke-width="1.4"/></svg>
  </div>
</header>
<nav class="main-nav">
  <ul>
    <li class="active">CANCER NEWS</li><li>NUTRITION DIAGNOSTICS</li><li>DIET STEPS</li><li>DIET SUPPLEMENTS IN CANCER</li><li>DICTIONARY OF MARKINGS ON FOOD</li><li>MERIBLEND VIDEOS</li><li>YOUR INDIVIDUAL DIET</li>
  </ul>
</nav>
<section class="hero" role="img" aria-label="Fresh berries, kiwi, citrus and supplement capsules">
  <div class="hero-caption">You are what you eat</div>
  <div class="hero-dots"><span></span><span></span><span></span><span class="on"></span></div>
</section>
<section class="welcome">
  <h1>Welcome to Vital Plate</h1>
  <p>Nullam accumsan purus vel tempus viverra. Mauris suscipit felis id nunc elementum varius. Praesent elementum nulla sit amet justo pellentesque scelerisque. Nam et tortor in ante iaculis porttitor in luctus mi. Vivamus gravida sem a pretium euismod. Nam lobortis, purus et fringilla tempus, risus eros dignissim diam, eget finibus sem risus sit amet eros. Vestibulum facilisis dolor at purus tincidunt porta. Nam fringilla nulla vel nisl condimentum, dapibus condimentum enim porta. Phasellus blandit quam a ipsum gravida dapibus. Cras sed augue tortor. Suspendisse elit ligula, iaculis dignissim justo eu, vestibulum venenatis</p>
</section>
<section class="news">
  <h2 class="section-title" style="top:21px">Cancer News</h2>
  <div class="arrows" style="top:32px">
    <svg width="6" height="8" viewBox="0 0 6 8"><path d="M4.5 1 1.5 4l3 3" fill="none" stroke="#444" stroke-width="1.4"/></svg>
    <svg width="6" height="8" viewBox="0 0 6 8"><path d="M1.5 1l3 3-3 3" fill="none" stroke="#444" stroke-width="1.4"/></svg>
  </div>
  <div class="cards" style="top:67px">
    <article class="card"><div class="card-media" role="img" aria-label="Vegetable juice glass with carrots and apples on a table" style="background:linear-gradient(160deg,#6f9a3a,#c8552e 55%,#8aa4b0)"></div><p>Nunc sit amet consequat risus. Curabitur elit leo. In eleif end dui tellus, in scelerisque elit porttitor et.</p><span class="more">VIEW MORE</span></article>
    <article class="card"><div class="card-media" role="img" aria-label="Doctor holding a Vitamin D sign" style="background:linear-gradient(180deg,#e9e7e0,#f3eecc 60%,#e6e2d8)"></div><p>Nunc sit amet consequat risus. Curabitur elit leo. In eleif end dui tellus, in scelerisque elit porttitor et.</p><span class="more">VIEW MORE</span></article>
    <article class="card"><div class="card-media" role="img" aria-label="Broccoli facing a red cell cluster" style="background:linear-gradient(90deg,#dcdcdc,#4f8a2e 30%,#d8d8d8 55%,#a8162a 80%,#d6d6d6)"></div><p>Nunc sit amet consequat risus. Curabitur elit leo. In eleif end dui tellus, in scelerisque elit porttitor et.</p><span class="more">VIEW MORE</span></article>
  </div>
</section>
<section class="newsletter">
  <h2>Newsletter Subscribe</h2>
  <div class="field" style="left:327px">Name</div>
  <div class="field" style="left:483px">Email</div>
  <div class="btn">Subscribe</div>
</section>
<section class="videos">
  <h2 class="section-title" style="top:877px">MERIBLEND VIDEOS</h2>
  <div class="arrows" style="top:887px">
    <svg width="6" height="8" viewBox="0 0 6 8"><path d="M4.5 1 1.5 4l3 3" fill="none" stroke="#444" stroke-width="1.4"/></svg>
    <svg width="6" height="8" viewBox="0 0 6 8"><path d="M1.5 1l3 3-3 3" fill="none" stroke="#444" stroke-width="1.4"/></svg>
  </div>
  <div class="cards" style="top:922px">
    <article class="card"><div class="card-media" role="img" aria-label="Video still of red blood cells" style="background:linear-gradient(135deg,#7a0f12,#c8262a 50%,#8e1416)"><svg class="play" width="16" height="16" viewBox="0 0 16 16"><circle cx="8" cy="8" r="8" fill="rgba(0,0,0,.55)"/><path d="M6.5 5v6l5-3z" fill="#fff"/></svg></div><p>Nunc sit amet consequat risus. Curabitur elit leo. In eleif end dui tellus, in scelerisque elit porttitor et.</p><span class="more">VIEW MORE</span></article>
    <article class="card"><div class="card-media" role="img" aria-label="Video still of a woman preparing juice in a kitchen" style="background:linear-gradient(90deg,#5a4a3a,#b08a5e 45%,#9a9890 75%,#6e5c48)"><svg class="play" width="16" height="16" viewBox="0 0 16 16"><circle cx="8" cy="8" r="8" fill="rgba(0,0,0,.55)"/><path d="M6.5 5v6l5-3z" fill="#fff"/></svg></div><p>Nunc sit amet consequat risus. Curabitur elit leo. In eleif end dui tellus, in scelerisque elit porttitor et.</p><span class="more">VIEW MORE</span></article>
    <article class="card"><div class="card-media" role="img" aria-label="Video still of a man speaking to camera" style="background:linear-gradient(90deg,#3e4a48,#b89a86 45%,#d8d6d0 70%,#8a8e8a)"><svg class="play" width="16" height="16" viewBox="0 0 16 16"><circle cx="8" cy="8" r="8" fill="rgba(0,0,0,.55)"/><path d="M6.5 5v6l5-3z" fill="#fff"/></svg></div><p>Nunc sit amet consequat risus. Curabitur elit leo. In eleif end dui tellus, in scelerisque elit porttitor et.</p><span class="more">VIEW MORE</span></article>
  </div>
</section>
<footer class="site-footer">
  <div class="footer-nav">CANCER NEWS<span>|</span>NUTRITION DIAGNOSTICS<span>|</span>DIET STEPS<span>|</span>DIET SUPPLEMENTS IN CANCER<span>|</span>DICTIONARY OF MARKINGS ON FOOD<span>|</span>MERIBLEND VIDEOS<span>|</span>YOUR INDIVIDUAL DIET</div>
  <div class="footer-rule"></div>
  <div class="copyright">Copyright &copy; 2015 &nbsp;Vital Plate. &nbsp;All rights reserved.</div>
  <div class="social" aria-label="Social links"><span></span><span></span><span></span><span></span><span></span><span></span><span></span><span></span></div>
</footer>
</body>
</html>
```